Redesign for a start up airline technology. The website is quelbrion.com.

I need a PowerPoint template that complements our website. I can provide our current template as a starting point.

```html
<!DOCTYPE html>
<html lang="en">
<head>
<meta charset="utf-8">
<title>Quelbrion – Presentation Template</title>
<link href="https://fonts.googleapis.com/css2?family=Anton&family=Roboto:wght@400;500;700&display=swap" rel="stylesheet">
<style>
:root{
  --canvas:#dedede;
  --white:#ffffff;
  --navy:#1a3d7c;
  --blue:#0b7bc1;
  --sky:#1e8fd0;
  --green:#7db23a;
  --green-dark:#2f7d32;
  --ink:#1b1b1b;
  --body:#444;
  --pill:#ececec;
  --blueprint:#05070c;
}
*{box-sizing:border-box;margin:0;padding:0}
html,body{width:1110px;height:1200px;overflow:hidden}
body{background:var(--canvas);font-family:'Roboto',sans-serif;position:relative}
.slide{position:absolute;width:449px;height:252px;background:var(--white);overflow:hidden;box-shadow:0 4px 14px rgba(0,0,0,.12)}
.col-left{left:77px}.col-right{left:584px}
.row-1{top:54px}.row-2{top:334px}.row-3{top:613px}.row-4{top:893px}
.layer{position:absolute;left:0;top:0;width:449px;height:252px}
.page-pill{position:absolute;right:0;top:227px;width:74px;height:19px;background:var(--pill);border-radius:10px 0 0 10px;font-size:7px;line-height:19px;padding-left:10px;color:var(--ink)}
.brand{position:absolute;display:flex;align-items:center;gap:5px;font-family:'Roboto',sans-serif;font-weight:700;letter-spacing:.5px}
.brand-dot{width:9px;height:9px;border-radius:50%;background:currentColor;opacity:1}
.brand-light{color:var(--white);font-size:18px}
.brand-dark{color:var(--navy);font-size:13px}
.heading{font-family:'Anton',sans-serif;font-weight:400;color:var(--ink)}
.slide-title{position:absolute;right:24px;top:5px;font-size:14px}
/* cover */
.cover-welcome{position:absolute;left:23px;top:200px;font-family:'Anton',sans-serif;font-size:15px;color:var(--blue)}
.cover-title{position:absolute;left:23px;top:216px;font-family:'Anton',sans-serif;font-size:24px;color:var(--navy)}
/* agenda */
.agenda-label{position:absolute;left:23px;top:110px;font-family:'Anton',sans-serif;font-size:14px;color:var(--white)}
.agenda-label::after{content:"";display:block;width:14px;height:1px;background:var(--white);margin-top:5px}
.agenda-list{position:absolute;left:280px;top:18px;list-style:none}
.agenda-list li{display:flex;align-items:center;height:28.8px;font-family:'Anton',sans-serif;font-size:8.5px;color:var(--ink)}
.agenda-num{width:15px;height:15px;border-radius:50%;color:var(--white);font-family:'Roboto',sans-serif;font-size:6.5px;display:flex;align-items:center;justify-content:center;margin-right:16px}
.num-green{background:var(--green)}.num-blue{background:var(--sky)}.num-navy{background:var(--navy)}
/* about */
.about-text{position:absolute;left:29px;top:76px;width:200px;font-size:6.4px;line-height:1.75;color:var(--body);text-align:justify}
.about-text p{margin-bottom:4px}
/* serve */
.serve-item{position:absolute;top:86px;width:120px;text-align:center}
.serve-item svg{display:block;margin:0 auto}
.serve-label{margin-top:8px;font-size:11px;font-weight:500;color:var(--ink)}
/* future */
.future-title{position:absolute;left:0;width:449px;top:76px;text-align:center;font-family:'Anton',sans-serif;font-size:21px;line-height:34px;color:var(--white)}
/* product */
.product-visual{position:absolute;left:0;top:0;width:208px;height:252px;background:var(--blueprint)}
.product-title{position:absolute;left:239px;top:62px;font-size:18px;line-height:21px}
.product-sub{position:absolute;left:239px;top:112px;font-size:11px;line-height:15px;color:var(--ink)}
.product-points{position:absolute;left:239px;top:150px;list-style:none;font-size:10.5px;color:var(--blue);line-height:19px}
.product-points li::before{content:"+";color:var(--green);font-weight:700;margin-right:7px}
/* sustainability */
.pledge-box{position:absolute;left:26px;top:79px;width:397px;height:138px;background:var(--white);text-align:center;padding:22px 28px 0}
.pledge-head{font-size:13.5px;line-height:21px}
.pledge-body{margin-top:9px;font-size:7.6px;line-height:14px;color:var(--ink)}
/* closing */
.closing-title{position:absolute;left:22px;top:203px;font-family:'Anton',sans-serif;font-size:27px;color:var(--navy)}
.contact{position:absolute;left:233px;display:flex;align-items:flex-start;gap:8px;font-size:8.8px;line-height:12.5px;color:var(--ink)}
.contact-address{top:195px}.contact-mail{top:227px}
</style>
</head>
<body>

<svg width="0" height="0" style="position:absolute">
  <defs>
    <linearGradient id="swoop" x1="0" x2="1" y1="0" y2="0">
      <stop offset="0" stop-color="#2f7d32"/><stop offset=".5" stop-color="#4d9a34"/><stop offset="1" stop-color="#9cc94a"/>
    </linearGradient>
    <linearGradient id="sky-photo" x1="0" x2="0" y1="0" y2="1">
      <stop offset="0" stop-color="#6fb65a"/><stop offset=".35" stop-color="#3d93b8"/><stop offset="1" stop-color="#2a6f9e"/>
    </linearGradient>
    <linearGradient id="city-photo" x1="0" x2="1" y1="0" y2="1">
      <stop offset="0" stop-color="#7eb850"/><stop offset=".4" stop-color="#2c8ec6"/><stop offset="1" stop-color="#1f5f96"/>
    </linearGradient>
  </defs>
</svg>

<!-- Cover -->
<section class="slide col-left row-1">
  <svg class="layer" viewBox="0 0 449 252">
    <path role="img" aria-label="Photo of a passenger jet taking off from a runway under a blue-green sky" d="M0 0H449V130C340 165 230 190 120 190C60 188 20 168 0 128Z" fill="url(#sky-photo)"/>
    <path d="M0 128C18 168 60 190 120 192C230 193 340 162 449 128L449 132C340 172 230 202 120 200C55 198 15 172 0 132Z" fill="url(#swoop)"/>
  </svg>
  <div class="brand brand-light" style="left:28px;top:18px"><span class="brand-dot"></span>Quelbrion</div>
  <div class="cover-welcome">Welcome To</div>
  <div class="cover-title">Airline Technology</div>
  <div class="page-pill">Page No : 01</div>
</section>

<!-- Agenda -->
<section class="slide col-left row-2">
  <svg class="layer" viewBox="0 0 449 252">
    <rect role="img" aria-label="Photo of two smiling pilots in a cockpit" x="120" y="0" width="169" height="252" fill="#8a7a6e"/>
    <path d="M0 0H150C115 40 115 80 130 130C148 180 155 220 150 252H0Z" fill="var(--sky)"/>
    <path d="M150 0C115 40 115 80 130 130C148 180 155 220 150 252H156C162 220 155 180 137 130C122 80 122 40 158 0Z" fill="var(--green)"/>
  </svg>
  <div class="agenda-label">Agenda</div>
  <div class="brand brand-light" style="left:23px;top:207px;font-size:15px"><span class="brand-dot"></span>Quelbrion</div>
  <ol class="agenda-list">
    <li><span class="agenda-num num-green">1</span>Home</li>
    <li><span class="agenda-num num-blue">2</span>About Us</li>
    <li><span class="agenda-num num-navy">3</span>Who We Are</li>
    <li><span class="agenda-num num-green">4</span>Who We Serve</li>
    <li><span class="agenda-num num-blue">5</span>Sustainability</li>
    <li><span class="agenda-num num-navy">6</span>News</li>
    <li><span class="agenda-num num-green">7</span>Contact Us</li>
    <li><span class="agenda-num num-blue">8</span>Thank You</li>
  </ol>
  <div class="page-pill">Page No : 02</div>
</section>

<!-- About -->
<section class="slide col-left row-3">
  <svg class="layer" viewBox="0 0 449 252">
    <path d="M0 22C30 45 70 65 150 64C260 58 370 40 449 22L449 25C370 44 260 62 150 68C75 70 28 52 0 22Z" fill="url(#swoop)"/>
    <circle cx="331" cy="154" r="86" fill="none" stroke="var(--green)" stroke-width="3"/>
    <circle role="img" aria-label="Photo of an aircraft technician inspecting landing gear" cx="331" cy="154" r="83" fill="#7a5a48"/>
  </svg>
  <div class="brand brand-dark" style="left:40px;top:18px"><span class="brand-dot"></span>Quelbrion</div>
  <h2 class="heading slide-title">About Us</h2>
  <div class="about-text">
    <p>Quelbrion is an aerospace technology company that produces a game changing onboard weight and balance measurement system - the Gear Load Sensing System (GLSS). The GLSS hardware kit automatically calculates an aircraft's weight and center of gravity for each flight.</p>
    <p>With numerous design, process and method patents, Quelbrion brings a unique combination of engineering innovation and certification expertise within the airline and aerospace industries.</p>
    <p>The Quelbrion leadership team holds decades of airline and relevant aviation experience, including a FAA delegated authority in the areas of Electrical Systems and Certification Management as a Designated Engineering Representative (DER).</p>
  </div>
  <div class="page-pill">Page No : 03</div>
</section>

<!-- Who We Serve -->
<section class="slide col-left row-4">
  <svg class="layer" viewBox="0 0 449 252">
    <path d="M0 22C30 45 70 65 150 64C260 58 370 40 449 22L449 25C370 44 260 62 150 68C75 70 28 52 0 22Z" fill="url(#swoop)"/>
  </svg>
  <div class="brand brand-dark" style="left:40px;top:18px"><span class="brand-dot"></span>Quelbrion</div>
  <h2 class="heading slide-title">Who We Serve</h2>

  <div class="serve-item" style="left:44px">
    <svg width="84" height="96" viewBox="0 0 84 96">
      <path d="M42 2L82 25V71L42 94L2 71V25Z" fill="var(--green)"/>
      <g fill="none" stroke="#fff" stroke-width="2" stroke-linecap="round">
        <circle cx="42" cy="48" r="16"/>
        <path d="M34 50L50 44M46 40L42 56M36 46L38 52"/>
      </g>
    </svg>
    <div class="serve-label">Commercial Aviation</div>
  </div>
  <div class="serve-item" style="left:170px">
    <svg width="84" height="96" viewBox="0 0 84 96">
      <path d="M42 2L82 25V71L42 94L2 71V25Z" fill="var(--sky)"/>
      <g fill="none" stroke="#fff" stroke-width="2" stroke-linecap="round" stroke-linejoin="round">
        <path d="M24 40H58C62 40 62 46 58 46H24L20 36Z"/>
        <path d="M38 40L32 30M40 46L34 54"/>
        <rect x="28" y="58" width="28" height="5"/><rect x="28" y="66" width="28" height="5"/>
      </g>
    </svg>
    <div class="serve-label">Business Aviation</div>
  </div>
  <div class="serve-item" style="left:296px">
    <svg width="84" height="96" viewBox="0 0 84 96">
      <path d="M42 2L82 25V71L42 94L2 71V25Z" fill="var(--navy)"/>
      <g fill="none" stroke="#fff" stroke-width="2" stroke-linecap="round" stroke-linejoin="round">
        <path d="M42 28L58 34V48C58 58 50 64 42 68C34 64 26 58 26 48V34Z"/>
        <path d="M35 47L40 52L50 41"/>
      </g>
    </svg>
    <div class="serve-label">Military</div>
  </div>
  <div class="page-pill">Page No : 04</div>
</section>

<!-- Future -->
<section class="slide col-right row-1" style="background:#1560a8">
  <svg class="layer" viewBox="0 0 449 252">
    <rect role="img" aria-label="Photo of engineers working on a jet engine, tinted blue" width="449" height="252" fill="#1560a8"/>
    <rect width="449" height="252" fill="#0b73bf" opacity=".45"/>
  </svg>
  <div class="brand brand-light" style="left:26px;top:18px;font-size:15px"><span class="brand-dot"></span>Quelbrion</div>
  <h1 class="future-title">Unlocking the<br>Future of Airline Operations<br>and the Flying Experience</h1>
  <div class="page-pill">Page No : 05</div>
</section>

<!-- Product -->
<section class="slide col-right row-2">
  <div class="product-visual" role="img" aria-label="Technical blueprint drawing of aircraft landing gear on a dark grid"></div>
  <div class="brand brand-dark" style="left:345px;top:18px"><span class="brand-dot"></span>Quelbrion</div>
  <h2 class="heading product-title">The Gear Load<br>Sensing System</h2>
  <p class="product-sub">An automated onboard weight<br>and balance measurement system</p>
  <ul class="product-points">
    <li>27 Patents (Awarded and Pending)</li>
    <li>Over 3,000 Commercial Flights</li>
  </ul>
  <div class="page-pill">Page No : 06</div>
</section>

<!-- Sustainability -->
<section class="slide col-right row-3" style="background:var(--green)">
  <svg class="layer" viewBox="0 0 449 252">
    <path d="M0 0H449V22C370 42 260 60 150 66C72 70 28 50 0 22Z" fill="var(--white)"/>
    <path d="M0 22C30 48 70 66 150 66C260 62 370 42 449 22L449 34C370 52 260 70 150 76C75 78 28 60 0 22Z" fill="url(#swoop)"/>
  </svg>
  <div class="brand brand-dark" style="left:40px;top:18px"><span class="brand-dot"></span>Quelbrion</div>
  <h2 class="heading slide-title">Sustainability</h2>
  <div class="pledge-box">
    <h3 class="heading pledge-head">We are dedicated to helping our customers achieve zero<br>carbon emissions by 2050.</h3>
    <p class="pledge-body">Our next-generation technology focuses on improving fuel burn efficiency to significantly reduce CO2 emissions from aircraft, promote sustainability, streamline operations, and contribute to a greener aviation industry.</p>
  </div>
  <div class="page-pill">Page No : 07</div>
</section>

<!-- Closing -->
<section class="slide col-right row-4">
  <svg class="layer" viewBox="0 0 449 252">
    <path role="img" aria-label="Photo of a jet flying between glass office towers, tinted blue and green" d="M0 0H449V128C340 160 240 184 140 188C70 190 20 130 0 72Z" fill="url(#city-photo)"/>
    <path d="M0 72C20 140 70 190 140 190C240 186 340 162 449 128L449 134C340 172 240 198 140 198C60 198 15 145 0 80Z" fill="url(#swoop)"/>
  </svg>
  <div class="brand brand-light" style="left:26px;top:22px;font-size:19px"><span class="brand-dot"></span>Quelbrion</div>
  <div class="closing-title">Thank You</div>
  <div class="contact contact-address">
    <svg width="14" height="18" viewBox="0 0 14 18"><path d="M7 0C3 0 0 3 0 7C0 12 7 18 7 18S14 12 14 7C14 3 11 0 7 0Z" fill="var(--sky)"/><circle cx="7" cy="7" r="2.6" fill="#fff"/></svg>
    <span>4170 Harlow Ave. Suite 300 Dallas,<br>Texas 75219</span>
  </div>
  <div class="contact contact-mail">
    <svg width="20" height="16" viewBox="0 0 20 16"><rect x="1" y="4" width="18" height="11" fill="none" stroke="var(--sky)" stroke-width="1.6"/><path d="M1 4L10 11L19 4" fill="none" stroke="var(--sky)" stroke-width="1.6"/><path d="M7 3L9.5 5.5L14 0.8" fill="none" stroke="var(--navy)" stroke-width="1.6"/></svg>
    <span style="padding-top:1px">info@quelbrion.com</span>
  </div>
  <div class="page-pill">Page No : 08</div>
</section>

</body>
</html>
```